Visitenkarten und Briefpapier
Zielgruppe
Planung und Realisierung von individuellen und wertbeständigen Kamin- und Ofenlösungen, sowie Fliesen- und Baddesign.
Aufgabenstellung
Wir benötigen ein möglichst schlichtes Design für Visitenkarten, bzw. Briefpapier. Für die Visitenkarten gerne auch Vorschläge mit Prägung, Ausstanzung oder mit Heißfolie. Auch Klappkarten wären denkbar. Das Design soll "das gewisse Etwas haben" und nicht zu verspielt sein.
Die Visitenkarten sind für die Firma KORVA, das Logo von der Ausstellung "raumfunke" soll dezent mit eingebunden werden (bei dem Briefpapier z.B. in der Fußzeile". Die farbliche Gestaltung sollte sich an den Farben des Logos orientieren.
Schriftart für Texte: Century Gothic
Schriftfarbe: RAL 7016
Nur eine Idee: Ich könnte mir auch gut vorstellen, dass die Visitenkarte aus einer Zündholzverpackung (wenn dann aber eine besondere mit nur einem Zündholz oder einem besonders breiten) besteht: http://glimmvelo.de/produkte_briefchen.php

```html
<!DOCTYPE html>
<html lang="de">
<head>
<meta charset="utf-8">
<title>KORVA – Visitenkarte</title>
<link rel="stylesheet" href="https://fonts.googleapis.com/css2?family=Questrial&display=swap">
<style>
  :root {
    --page: #e4e4e2;
    --anthracite: #1d2a30;
    --anthracite-soft: #2c3a41;
    --paper: #ececec;
    --ink: #111111;
    --flame: #d9820f;
    --text-light: #c9cccd;
    --text-muted: #8a9296;
    --font: "Questrial", "Century Gothic", sans-serif;
  }
  * { box-sizing: border-box; margin: 0; padding: 0; }
  html, body { width: 1200px; height: 840px; overflow: hidden; }
  body { background: var(--page); font-family: var(--font); position: relative; }

  .card {
    position: absolute; top: 252px; width: 520px; height: 336px;
    overflow: hidden; box-shadow: 0 10px 30px rgba(0,0,0,.22);
  }
  .card--back { left: 60px; background: linear-gradient(135deg, var(--anthracite-soft), var(--anthracite) 70%); }
  .card--front { left: 620px; background: var(--anthracite); }

  /* front */
  .brand { position: absolute; left: 0; right: 0; text-align: center; }
  .brand__name { font-size: 104px; letter-spacing: 10px; color: var(--text-light); line-height: 1; }
  .brand__tagline { font-size: 25px; letter-spacing: 2px; color: var(--text-light); margin-top: 6px; }
  .card--front .brand { top: 92px; }
  .partner { position: absolute; right: 26px; bottom: 22px; font-size: 15px; letter-spacing: 1px; color: var(--text-muted); }

  /* back */
  .back__swoosh { position: absolute; inset: 0; }
  .card--back .brand { left: 28px; right: auto; top: 26px; text-align: left; }
  .card--back .brand__name { font-size: 64px; letter-spacing: 6px; color: var(--ink); }
  .card--back .brand__tagline { font-size: 15px; letter-spacing: 1px; color: var(--ink); margin-top: 2px; }

  .address { position: absolute; left: 28px; top: 176px; display: flex; gap: 8px; color: var(--text-light); font-size: 15px; line-height: 1.35; }
  .address svg { width: 14px; height: 18px; margin-top: 1px; flex: none; }

  .person { position: absolute; right: 28px; top: 176px; text-align: right; }
  .person__name { font-size: 28px; color: var(--flame); line-height: 1.1; }
  .person__role { font-size: 15px; color: var(--text-light); margin-top: 2px; }

  .contact { position: absolute; right: 28px; bottom: 22px; list-style: none; text-align: right; }
  .contact li { display: flex; justify-content: flex-end; align-items: center; gap: 10px; font-size: 15px; color: var(--text-light); line-height: 1.55; }
  .contact svg { width: 16px; height: 16px; flex: none; }
</style>
</head>
<body>

<section class="card card--back" aria-label="Visitenkarte Rückseite">
  <svg class="back__swoosh" viewBox="0 0 520 336" aria-hidden="true">
    <path d="M0 0 H392 C380 118 300 168 196 162 C118 158 52 132 0 100 Z" fill="var(--paper)"/>
    <path d="M0 100 C52 132 118 158 196 162 C300 168 380 118 392 0" fill="none" stroke="var(--flame)" stroke-width="5"/>
    <path d="M0 96 C56 126 122 150 196 154 C292 158 366 114 386 0" fill="none" stroke="var(--ink)" stroke-width="3"/>
  </svg>

  <div class="brand">
    <div class="brand__name">KORVA</div>
    <div class="brand__tagline">kamine · öfen · fliesen</div>
  </div>

  <div class="address">
    <svg viewBox="0 0 14 18" aria-hidden="true"><path d="M7 0a7 7 0 0 0-7 7c0 5 7 11 7 11s7-6 7-11a7 7 0 0 0-7-7zm0 9.5A2.5 2.5 0 1 1 7 4.5a2.5 2.5 0 0 1 0 5z" fill="var(--text-light)"/></svg>
    <p>Am Lindenhang 12<br>34519 Tannfeld</p>
  </div>

  <div class="person">
    <p class="person__name">Jonas Merten</p>
    <p class="person__role">Geschäftsführer</p>
  </div>

  <ul class="contact">
    <li>05642 / 71 38 40
      <svg viewBox="0 0 16 16" aria-hidden="true"><path d="M3 1l3 3-1.5 2a9 9 0 0 0 5.5 5.5L12 10l3 3-2 2C7 15 1 9 1 3z" fill="none" stroke="var(--text-light)" stroke-width="1.3"/></svg></li>
    <li>05642 / 71 38 48
      <svg viewBox="0 0 16 16" aria-hidden="true"><rect x="4" y="1" width="8" height="4" fill="none" stroke="var(--text-light)" stroke-width="1.2"/><rect x="1" y="5" width="14" height="7" fill="var(--text-light)"/><rect x="4" y="10" width="8" height="5" fill="var(--anthracite)" stroke="var(--text-light)" stroke-width="1.2"/></svg></li>
    <li>info@korva-tannfeld.de
      <svg viewBox="0 0 16 16" aria-hidden="true"><rect x="1" y="3" width="14" height="10" fill="none" stroke="var(--text-light)" stroke-width="1.2"/><path d="M1 3l7 6 7-6" fill="none" stroke="var(--text-light)" stroke-width="1.2"/></svg></li>
  </ul>
</section>

<section class="card card--front" aria-label="Visitenkarte Vorderseite">
  <div class="brand">
    <div class="brand__name">KORVA</div>
    <div class="brand__tagline">kamine · öfen · fliesen</div>
  </div>
  <p class="partner">raumfunke</p>
</section>

</body>
</html>
```